COVER ONLY - Electrical supply company needs new catalogue cover (front and back)

We're currently finalising our catalogue and have gone through many changes in branding since our last catalogue so need a completely NEW design incorporating the new logo and design feel from the CI document attached.

Since the company is moving more corporate we'd like a much cleaner looking cover (front and back) from what we had before. We'd would like to keep a dominate color for the year so we can simply change the color for the following year catalogue.

We'd like to show product images (supplied) on the front of the catalogue but not as dominate as our previous catalogue (attached to get an idea of where we came from).

We'd like to introduce as much of our new CI into the new catalogue cover as possible while keeping up with our new corporate style of "clean and neat".

I've attached our logo, CI guide, old catalogue cover and some product images.

We would like the file to be handed over in complete format as well as in .psd

(Our website is also being updated but the old website is still up www.qv.co.za)
Updates

Cover size is A4 and the spine will be roughly 3/4 inch.

Please make sure you read the CI guide.

Produce something that shows professionalism, class and style.  We want something that any multi national billion dollar company would be proud to show

Industry/Entity Type

Electrical

Font styles to use
Other font styles liked:
• Sansation

```html
<!DOCTYPE html>
<html lang="en">
<head>
<meta charset="utf-8">
<title>QuanVolt Catalogue Cover</title>
<link href="https://fonts.googleapis.com/css2?family=Open+Sans:ital,wght@0,400;0,600;0,700;1,400&display=swap" rel="stylesheet">
<style>
  :root {
    --teal: #2fb3c8;
    --teal-light: #8fd9e4;
    --teal-pale: #c9eef3;
    --charcoal: #4a4b4f;
    --charcoal-dark: #35363a;
    --ink: #1e1e1e;
    --white: #ffffff;
    --stage: #e4e4e4;
  }
  * { margin: 0; padding: 0; box-sizing: border-box; }
  html, body { width: 1200px; height: 683px; overflow: hidden; }
  body {
    background: var(--stage);
    font-family: "Open Sans", Arial, sans-serif;
    position: relative;
  }
  .spread {
    position: absolute; left: 148px; top: 21px;
    width: 904px; height: 640px; display: flex;
    box-shadow: 0 6px 24px rgba(0,0,0,.18);
  }
  .cover { position: relative; width: 452px; height: 640px; overflow: hidden; background: var(--white); }
  .cover svg.bg { position: absolute; inset: 0; }

  /* back cover */
  .back-visual {
    position: absolute; left: 0; top: 0; width: 452px; height: 500px;
    background: linear-gradient(160deg, var(--teal-pale) 0%, var(--teal) 45%, #1f9fb6 100%);
  }
  .range { position: absolute; left: 30px; top: 34px; width: 392px; color: var(--white); font-size: 8.5px; line-height: 1.35; }
  .range h3 { font-size: 10.5px; font-weight: 700; margin-top: 7px; }
  .range h4 { font-size: 9.5px; font-weight: 400; margin-top: 5px; }
  .range p { font-style: italic; }
  .range .brands { margin-top: 8px; }
  .contact-title { position: absolute; left: 250px; top: 458px; font-size: 22px; font-weight: 700; color: var(--ink); }
  .contact-block { position: absolute; color: var(--ink); font-size: 11.5px; line-height: 1.4; font-style: normal; }
  .contact-durban { left: 250px; top: 492px; }
  .contact-cape { left: 40px; top: 540px; font-size: 12.5px; }

  /* front cover */
  .brand { position: absolute; left: 26px; top: 22px; display: flex; align-items: center; gap: 8px; }
  .brand-mark { width: 16px; height: 16px; background: var(--teal); }
  .brand-name { font-size: 20px; font-weight: 600; color: var(--teal); }
  .tagline {
    position: absolute; right: 24px; top: 72px; width: 280px;
    text-align: right; color: var(--white); font-size: 15px; line-height: 1.25;
  }
  .tagline strong { color: var(--teal-light); font-weight: 700; }
  .product-photo {
    position: absolute; left: 92px; top: 132px; width: 270px; height: 270px; border-radius: 50%;
    background: radial-gradient(circle at 45% 40%, #e9eef0 0%, #b9c4c8 45%, #6f7a80 100%);
  }
  .web { position: absolute; right: 24px; bottom: 26px; font-size: 11px; font-weight: 600; color: var(--charcoal); }
</style>
</head>
<body>
<main class="spread">

  <section class="cover cover-back">
    <div class="back-visual" role="img" aria-label="Teal circuit board lines over a faint world map"></div>
    <svg class="bg" width="452" height="640" viewBox="0 0 452 640" aria-hidden="true">
      <path d="M0 495 C 130 455, 300 420, 452 428 L452 640 L0 640 Z" fill="var(--white)"/>
      <path d="M0 495 C 130 455, 300 420, 452 428" fill="none" stroke="var(--teal-light)" stroke-width="3"/>
    </svg>
    <div class="range">
      <h3>A - relays</h3>
      <p>PCB, plug-in, timing, miniature, industrial and power relays, relay interfaces, sockets, daylight switches, solid-state relays and accessories</p>
      <p>Brands: Fintra, Celvar</p>
      <h3>B - motor control</h3>
      <h4>Control and protection</h4>
      <p>• Contactors • Semiconductor contactors • Thermal overload relays • Motor control circuit breakers • Motor starters • Soft starters • IC soft starters • Electronic motor protection</p>
      <h4>Command and signalling</h4>
      <p>• Pushbuttons and selectors • Signal towers and beacons • Limit and roof switches • Rotary cam switches • Joystick controls • Pendant controls • Wormgear limit switches</p>
      <h4>Switching and circuit protection</h4>
      <p>• Load break switches • Earth leakage relays</p>
      <h4>Automation and control</h4>
      <p>• Time relays • Protection relays • Level control relays • Programmable logic relays • Switching power supplies</p>
      <h4>Energy management</h4>
      <p>• Metering instruments (kWh) • Automatic power factor controllers • Automatic battery chargers • Automatic transfer switch controllers • Engine and generator controllers</p>
      <p class="brands">Brands: Lumaro, Tevra, Fanvik, IC Dynamic</p>
    </div>
    <h2 class="contact-title">Contact</h2>
    <address class="contact-block contact-durban">
      P.O. Box 40218<br>Marlow Bay<br>4102 Harbourside<br>Telephone: 011 555 0142<br>Telefax: 011 555 0187<br>Email: info@qv.co.za
    </address>
    <address class="contact-block contact-cape">
      Cape Province<br>14 Alderwood Commercial Park<br>Linden Road<br>Riverside Gardens<br>Westport 7520
    </address>
  </section>

  <section class="cover cover-front">
    <svg class="bg" width="452" height="640" viewBox="0 0 452 640" aria-hidden="true">
      <path d="M0 120 C 150 40, 320 40, 452 55 L452 560 L0 560 Z" fill="var(--charcoal)"/>
      <circle cx="227" cy="267" r="205" fill="var(--charcoal-dark)"/>
      <circle cx="227" cy="267" r="185" fill="none" stroke="var(--teal)" stroke-width="22"/>
      <circle cx="227" cy="267" r="160" fill="var(--teal-pale)" opacity=".55"/>
      <path d="M0 500 C 150 560, 330 470, 452 420 L452 640 L0 640 Z" fill="var(--teal)"/>
      <path d="M0 525 C 160 585, 330 500, 452 455 L452 640 L0 640 Z" fill="var(--teal-light)"/>
      <path d="M0 545 C 170 605, 330 525, 452 485 L452 640 L0 640 Z" fill="var(--white)"/>
    </svg>
    <div class="brand"><span class="brand-mark"></span><span class="brand-name">QuanVolt</span></div>
    <p class="tagline">Dedicated supliers of <strong>quality products &amp; sevice at</strong> competitivew prices</p>
    <div class="product-photo" role="img" aria-label="Product group: variable speed drive, moulded case circuit breaker, controller unit and socket"></div>
    <p class="web">www.qv.co.za</p>
  </section>

</main>
</body>
</html>
```